Quorbelline.io - Please redesign to make it look better from current design

We already have the current website, that you can access but we think it can improve from current version.
Quorbelline is a cryptocurrency hedge fund that allow you to participate in the hedge fund with cryptocurrency such as eth.
At current phase, we are doing an ICO, then we want to make sure that the website it looks professional, beautiful and trustable enough for investors after looking at our website.
Target Market(s)
Investors
Industry/Entity Type
Investment
Coding
Coded - Design and coding required
Number of Pages Required
1 page
Look and feel
Each slider illustrates characteristics of the customer's brand and the style your logo design should communicate.

```html
<!DOCTYPE html>
<html lang="en">
<head>
<meta charset="utf-8">
<title>Quorbelline — Digital Asset Management</title>
<link rel="stylesheet" href="https://fonts.googleapis.com/css2?family=Mulish:wght@400;600;700&display=swap">
<style>
:root{
  --hero-deep:#0b5fb8;
  --hero-light:#4aa8e8;
  --navy:#1e56a0;
  --sky:#2a8fd0;
  --grey-bg:#efefef;
  --text:#333;
  --muted:#777;
  --band-dark:#0a4fa6;
  --band-light:#2c7fd4;
  --footer:#2d9fd9;
  --white:#fff;
}
*{margin:0;padding:0;box-sizing:border-box}
html,body{width:1200px;height:2885px;overflow:hidden}
body{font-family:"Mulish",sans-serif;color:var(--text);background:var(--white);position:relative}
section,header,footer{position:absolute;left:0;width:1200px}
.abs{position:absolute}
.center{left:0;width:1200px;text-align:center}

/* hero */
.hero{top:0;height:677px}
.hero-bg{position:absolute;inset:0;background:linear-gradient(135deg,var(--hero-deep) 0%,#1c86d6 50%,var(--hero-light) 100%)}
.brand{left:106px;top:52px;display:flex;align-items:center;gap:14px;color:var(--white);font-size:30px;font-weight:700;letter-spacing:1px}
.brand-dot{width:34px;height:34px;border-radius:50%;background:var(--white)}
.main-nav{left:465px;top:66px;display:flex;gap:0}
.main-nav a{color:var(--white);text-decoration:none;font-size:18px;margin-right:44px}
.hero-title{top:276px;font-size:46px;font-weight:700;color:var(--white)}
.hero-sub{top:338px;font-size:21px;font-weight:600;line-height:29px;color:var(--white)}
.btn-outline-light{left:512px;top:419px;width:178px;height:48px;border:2px solid var(--white);color:var(--white);font-size:18px;font-weight:600;display:flex;align-items:center;justify-content:center}
.slider-dots{top:622px;display:flex;justify-content:center;gap:9px}
.slider-dots span{width:14px;height:14px;border-radius:50%;background:var(--white)}
.slider-dots span.active{background:transparent;border:2px solid var(--white)}

/* section titles */
.section-title{font-size:38px;font-weight:400}
.rule{height:2px;width:110px;left:545px;background:#c8c8c8}

/* about */
.about{top:677px;height:406px;background:var(--grey-bg);border-bottom:1px solid #d8d8d8}
.about .section-title{top:54px;color:var(--navy)}
.about .rule{top:110px}
.about-text{left:210px;width:780px;top:142px;font-size:14.5px;line-height:25px;color:var(--muted);text-align:center}
.about-text p+p{margin-top:4px}
.btn-outline{border:2px solid var(--navy);color:var(--navy);font-size:14px;font-weight:700;display:flex;align-items:center;justify-content:center}
.about .btn-outline{left:529px;top:308px;width:142px;height:36px}

/* team */
.team{top:1083px;height:467px;background:var(--white);border-bottom:1px solid #d0d0d0}
.team .section-title{top:52px;color:var(--sky);font-size:33px}
.team .rule{top:97px;width:80px;left:560px}
.member{top:124px;width:280px;text-align:center}
.portrait{width:212px;height:212px;margin:0 auto;border-radius:50%;border:2px solid var(--sky);padding:6px}
.portrait div{width:100%;height:100%;border-radius:50%;background:radial-gradient(circle at 50% 45%,#c9a58a 0%,#8a6a55 55%,#4a3a32 100%)}
.member-name{margin-top:16px;font-size:19px;font-weight:600;color:#111}
.member-role{margin-top:6px;font-size:16px;font-weight:600;color:var(--navy)}

/* process */
.process{top:1550px;height:469px;background:#f3f3f3}
.process-photo{left:0;top:0;width:600px;height:469px;background:linear-gradient(90deg,#8a7058 0%,#b9a58e 45%,#e0dad2 80%,#f3f3f3 100%)}
.process h2{left:571px;top:84px;font-size:35px;font-weight:400;color:#333}
.process h3{left:575px;top:142px;font-size:16px;font-weight:600;color:var(--navy)}
.process-text{left:575px;top:172px;width:510px;font-size:14.5px;line-height:25px;color:var(--muted)}
.process .btn-outline{left:575px;top:327px;width:142px;height:38px}

/* distribution */
.distribution{top:2019px;height:304px;background:linear-gradient(180deg,var(--band-dark) 0%,var(--band-light) 100%)}
.distribution h2{top:68px;font-size:30px;font-weight:600;color:var(--white)}
.dist-col{top:135px;width:320px;list-style:none;color:var(--white);font-size:14.5px;line-height:19px}
.dist-col li{position:relative;padding-left:22px;margin-bottom:14px}
.dist-col li::before{content:"";position:absolute;left:4px;top:5px;border-left:6px solid var(--white);border-top:4px solid transparent;border-bottom:4px solid transparent}

/* white papers */
.papers{top:2323px;height:392px}
.papers-photo{position:absolute;inset:0;background:linear-gradient(90deg,#e8e4dc 0%,#f4f3f0 35%,#f4f3f0 70%,#e2e2e2 100%)}
.papers h2{top:106px;font-size:35px;font-weight:400;color:#333}
.papers-text{top:160px;font-size:15px;line-height:27px;color:var(--muted)}
.btn-solid{left:537px;top:235px;width:150px;height:38px;background:var(--sky);color:var(--white);font-size:15px;display:flex;align-items:center;justify-content:center}

/* footer */
.site-footer{top:2715px;height:170px;background:var(--footer)}
.footer-nav{left:117px;top:42px;display:flex}
.footer-nav a{color:var(--white);text-decoration:none;font-size:18px;margin-right:44px}
.copyright{left:117px;top:87px;font-size:13px;color:var(--white)}
.social{left:914px;top:42px;display:flex;gap:10px}
.social span{width:36px;height:36px;border-radius:50%;border:2px solid var(--white)}
</style>
</head>
<body>

<header class="hero">
  <div class="hero-bg" role="img" aria-label="Blue financial chart background with trading grid lines"></div>
  <div class="abs brand"><span class="brand-dot"></span>quorbelline</div>
  <nav class="abs main-nav">
    <a href="#">Home</a><a href="#">About Us</a><a href="#">Services</a><a href="#">Team</a><a href="#">Process</a><a href="#">Contact</a>
  </nav>
  <h1 class="abs center hero-title">Digital Asset Management</h1>
  <p class="abs center hero-sub">Quorbelline enable companies and investors to facilities business operation in modern<br>digital world, including asset management on hedge fund strategy model.</p>
  <a class="abs btn-outline-light">READ MORE</a>
  <div class="abs center slider-dots"><span class="active"></span><span></span><span></span><span></span></div>
</header>

<section class="about">
  <h2 class="abs center section-title">About Quorbelline</h2>
  <div class="abs rule"></div>
  <div class="abs about-text">
    <p>Quorbelline process and manages on hedge fund strategy models which invests in a diversified portfolio of blockchain tokens. Blockchain tokens are emerging which add a monetary incentive layer to p2p protocols and facilitate equity crowdfunding that anyone in the world can participate in.</p>
    <p>This means open source software developers can monetize their networks at the protocol level and users of the network are the equity owners of the network. For this conditions, returns will go to holders of the tokens.</p>
  </div>
  <a class="abs btn-outline">READ MORE</a>
</section>

<section class="team">
  <h2 class="abs center section-title">Our Team</h2>
  <div class="abs rule"></div>
  <div class="abs member" style="left:131px">
    <div class="portrait"><div role="img" aria-label="Portrait photo of the director"></div></div>
    <p class="member-name">Dalvren Oskutari</p>
    <p class="member-role">Director</p>
  </div>
  <div class="abs member" style="left:458px">
    <div class="portrait"><div role="img" aria-label="Portrait photo of the technical advisor"></div></div>
    <p class="member-name">Telmar Quenbrey</p>
    <p class="member-role">Technical advisor</p>
  </div>
  <div class="abs member" style="left:781px">
    <div class="portrait"><div role="img" aria-label="Portrait photo of the marketing consultant"></div></div>
    <p class="member-name">Variel Ostrandhome</p>
    <p class="member-role">Marketing Consultant</p>
  </div>
</section>

<section class="process">
  <div class="abs process-photo" role="img" aria-label="Desk with a computer monitor showing a progress report, keyboard and office items"></div>
  <h2 class="abs">Our Process</h2>
  <h3 class="abs">Hedge Fund Model</h3>
  <p class="abs process-text">Quorbelline run on closed-end fund (CEF) model which offers its shares to investors and utilize the fund to speculate and invest in the innovative blockchain tokens. Quorbelline will charge an upfront annual operation fee 4% of the money raised during the ICO. After that, the fund will charge a quarterly performance of 50% on the net profit made.</p>
  <a class="abs btn-outline">READ MORE</a>
</section>

<section class="distribution">
  <h2 class="abs center">Net Profit Distribution</h2>
  <ul class="abs dist-col" style="left:119px">
    <li>50 % of net profit is distributed to investors</li>
    <li>0 – 5 % net profit &gt; 0% performance fee</li>
  </ul>
  <ul class="abs dist-col" style="left:462px">
    <li>5 – 10% net profit &gt; 5% performance fee</li>
    <li>10-15 % net profit &gt; 13% performance fee</li>
  </ul>
  <ul class="abs dist-col" style="left:785px">
    <li>&gt; 15% net profit &gt; 15% performance fee</li>
    <li>The remainder (50% minus performance fee, so at least 35%) is reinvested</li>
  </ul>
</section>

<section class="papers">
  <div class="papers-photo" role="img" aria-label="Light desk top with keyboard, plant, ruler, earphones and smartphone"></div>
  <h2 class="abs center">Download Our White Papers</h2>
  <p class="abs center papers-text">ullamcorper est eget tempor cursus neque mi consectetuer mi a ultricies massa est sed nisl<br>Class aptent taciti sociosqu ad litora torquent per conubia nostra per</p>
  <a class="abs btn-solid">Download</a>
</section>

<footer class="site-footer">
  <nav class="abs footer-nav">
    <a href="#">Home</a><a href="#">About Us</a><a href="#">Services</a><a href="#">Team</a><a href="#">Process</a><a href="#">Contact</a>
  </nav>
  <p class="abs copyright">© 2017 Company Name  All right reserved  Term of Use</p>
  <div class="abs social"><span></span><span></span><span></span><span></span></div>
</footer>

</body>
</html>
```